Granite Bureau of Analysis Card Design

I need a business card for the agency I currently am tasked with, which is based in Hartford, CT. GBAN provides, disseminates and obtains intelligence in regards to ongoing criminal investigations throughout the State of CT. The information we obtain and provide, comes to us and is sent out by various Law Enforcement agencies throughout CT.

Industry/Entity Type

Business

Contact Information for Business Card

Officer Lyle P. Harrowby
Bramford Police Department - Eastern Region Intelligence Officer
Granite Bureau of Analysis
4827 Willowmere Ave., Middletown, CT 06457
Work Cell: (555) 318-2694
E-Mail: gban.wd@gbanmail.example

```html
<!DOCTYPE html>
<html lang="en">
<head>
<meta charset="utf-8">
<title>Granite Bureau of Analysis – Business Card</title>
<link rel="stylesheet" href="https://fonts.googleapis.com/css2?family=Open+Sans:wght@400;600&family=Michroma&display=swap">
<style>
  :root {
    --backdrop: #e6e4e1;
    --card: #ffffff;
    --band-red: #c81b2e;
    --ink: #2a2a2a;
    --name-white: #ffffff;
  }
  html, body {
    margin: 0;
    width: 1200px;
    height: 941px;
    overflow: hidden;
    background: var(--backdrop);
  }
  .card-stage {
    position: absolute;
    left: 340px;
    top: 60px;
    width: 520px;
    height: 820px;
  }
  .card-face { fill: var(--card); }
  .band { fill: var(--band-red); }
  .holder-name {
    font-family: "Open Sans", sans-serif;
    font-weight: 400;
    font-size: 34px;
    fill: var(--name-white);
    letter-spacing: 0.5px;
  }
  .holder-title {
    font-family: "Open Sans", sans-serif;
    font-weight: 400;
    font-size: 23px;
    fill: var(--name-white);
  }
  .agency-mark {
    font-family: "Open Sans", sans-serif;
    font-weight: 600;
    font-size: 26px;
    fill: var(--ink);
  }
  .agency-square { fill: var(--band-red); }
  .contact-line {
    font-family: "Michroma", sans-serif;
    font-size: 14px;
    fill: var(--ink);
  }
</style>
</head>
<body>
  <div class="card-stage">
    <svg width="520" height="820" viewBox="-10 -10 520 820" xmlns="http://www.w3.org/2000/svg">
      <defs>
        <clipPath id="card-shape">
          <rect x="0" y="0" width="500" height="800" rx="42" ry="42"/>
        </clipPath>
        <filter id="card-lift" x="-10%" y="-10%" width="120%" height="120%">
          <feDropShadow dx="0" dy="3" stdDeviation="4" flood-opacity="0.18"/>
        </filter>
      </defs>

      <rect class="card-face" x="0" y="0" width="500" height="800" rx="42" ry="42" filter="url(#card-lift)"/>

      <g clip-path="url(#card-shape)">
        <g transform="translate(0 516) rotate(-30)">
          <rect class="band band-edge" x="-400" y="-72" width="1400" height="6"/>
          <rect class="band band-main" x="-400" y="-58" width="1400" height="116"/>
          <rect class="band band-edge" x="-400" y="66" width="1400" height="6"/>

          <rect class="agency-square" x="236" y="-126" width="24" height="24"/>
          <text class="agency-mark" x="270" y="-104">Bramford Police</text>

          <text class="holder-name" x="90" y="-10">LYLE P. HARROWBY</text>
          <text class="holder-title" x="150" y="26">Intelligence Officer</text>

          <text class="contact-line" x="30" y="102">4827 Willowmere Ave., Middletown</text>
          <text class="contact-line" x="30" y="134">(555) 318-2694</text>
          <text class="contact-line" x="30" y="166">gban.wd@gbanmail.example</text>
          <text class="contact-line" x="30" y="198">Granite Bureau of Analysis</text>
        </g>
      </g>
    </svg>
  </div>
</body>
</html>
```